Meridale Bed Company Needs Business Card

Looking for a very nice looking business card. Creative but not extravagant. We sell beds and pillows across the U.S. and need something professional but catchy. I have attached the logo.

Name : Devin Holt
Title : President
Phone : (800) 471-2960
Email: sleep@quilmora.com
Website: www.quilmora.com

Can be single-sided or double-sided
horizontal or vertical

Can use Blues/Greys

Target Market(s)

Mass Market

Industry/Entity Type

Retail

Contact Information for Business Card

Name : Devin Holt
Title : President
Phone : (800) 471-2960
Email: sleep@quilmora.com
Website: www.quilmora.com

Requirements
Must have
• Clean, Modern, Smooth
• Can use Blues/Greys
• On the other side without the information - have something simple like www.quilmora.com or our logo
Nice to have
• Surprise me
Should not have
• Nothing crazy, nothing cluttered

```html
<!DOCTYPE html>
<html lang="en">
<head>
<meta charset="utf-8">
<title>Meridale Bed Company — Business Card</title>
<link rel="stylesheet" href="https://fonts.googleapis.com/css2?family=Raleway:wght@300;400;700&display=swap">
<style>
  :root {
    --page-bg: #e9ecee;
    --card-white: #ffffff;
    --brand-blue: #2a9bd6;
    --brand-blue-deep: #1f7fc6;
    --ink-grey: #4a4f54;
    --ink-soft: #5d6368;
    --on-blue: #ffffff;
    --card-shadow: rgba(40, 60, 80, 0.18);
  }
  * { box-sizing: border-box; margin: 0; padding: 0; }
  html, body {
    width: 1200px;
    height: 900px;
    overflow: hidden;
    background: var(--page-bg);
    font-family: "Raleway", sans-serif;
  }
  .card-sheet {
    position: relative;
    width: 1200px;
    height: 900px;
    display: flex;
    align-items: center;
    justify-content: center;
    gap: 60px;
  }
  .card {
    position: relative;
    width: 500px;
    height: 286px;
    border-radius: 3px;
    box-shadow: 0 10px 24px var(--card-shadow);
    overflow: hidden;
  }
  .card--front { background: var(--card-white); }
  .card--back {
    background: linear-gradient(135deg, var(--brand-blue) 0%, #2fa2da 55%, var(--brand-blue-deep) 100%);
  }
  .wordmark {
    font-family: "Raleway", sans-serif;
    font-weight: 300;
    letter-spacing: 1px;
  }
  .card--front .wordmark {
    position: absolute;
    top: 30px;
    right: 34px;
    font-size: 30px;
    color: var(--brand-blue);
  }
  .contact-block {
    position: absolute;
    left: 40px;
    bottom: 34px;
  }
  .contact-name {
    font-weight: 700;
    font-size: 27px;
    color: var(--brand-blue);
    line-height: 1.1;
  }
  .contact-title {
    font-weight: 400;
    font-size: 20px;
    color: var(--ink-grey);
    margin-bottom: 14px;
  }
  .contact-line {
    font-weight: 400;
    font-size: 15px;
    color: var(--ink-soft);
    line-height: 1.5;
  }
  .card--back .wordmark {
    position: absolute;
    left: 0;
    right: 0;
    top: 96px;
    text-align: center;
    font-size: 56px;
    color: var(--on-blue);
  }
  .web-address {
    position: absolute;
    left: 0;
    right: 0;
    bottom: 40px;
    text-align: center;
    font-weight: 400;
    font-size: 13px;
    letter-spacing: 6px;
    color: var(--on-blue);
  }
</style>
</head>
<body>
  <main class="card-sheet">
    <section class="card card--front" aria-label="Card front">
      <div class="wordmark">quilmora</div>
      <div class="contact-block">
        <div class="contact-name">Devin Holt</div>
        <div class="contact-title">President</div>
        <div class="contact-line">(800) 471-2960</div>
        <div class="contact-line">sleep@quilmora.com</div>
      </div>
    </section>
    <section class="card card--back" aria-label="Card back">
      <div class="wordmark">quilmora</div>
      <div class="web-address">www.quilmora.com</div>
    </section>
  </main>
</body>
</html>
```